1" x 3" label needed for essential oil bottle(s) - new ecommerce company

We need a label designed for 10 ml bottles of essential oils. We are offering 9 different types of essential oil: Lavender, Cedarwood, Eucalyptus, Frankincense, Lemon, Orange, Peppermint, Rosemary, and Tea Tree. The label should have a space for the type of essential oil. The bottles are an amber color (am including a photo) as essential oils are sensitive to light. also am including an AI file of our logo, which we'd like included on the label; the logo file also contains our logo colors, a dark blue and light grey. We'd also like the following on the label: "CAUTION: EYE AND SKIN IRRITANT. Avoid contact with eyes and skin. Wash hands after handling. If eye contact occurs, flush with water for 15 minutes. Not intended for topical or internal use. Contains Essential Oils. KEEP OUT OF REACH OF CHILDREN."
Also "Ingredients: 100% pure essential oil, GC tested."
Also "0.33 fl oz (10 ml)
Finally, we will need to include a sideways bar code on the right side of the label, so need 3/8" of white space on the right of the label.
We'd like the label to be calming, but modern, friendly, and confident.

```html
<!DOCTYPE html>
<html lang="en">
<head>
<meta charset="utf-8">
<title>Solvera Essential Oil Labels</title>
<link rel="stylesheet" href="https://fonts.googleapis.com/css2?family=Saira+Condensed:wght@400;500;600;700&display=swap">
<style>
  :root {
    --page: #ffffff;
    --label-white: #f6f6f6;
    --label-edge: #e2e2e2;
    --ink: #2b2b2b;
    --ink-soft: #4a4a4a;
    --gold: #c9a65a;
    --gold-dark: #a88433;
    --rosemary: #e4467c;
    --peppermint: #c8952a;
    --eucalyptus: #2f9935;
    --teatree: #2f9935;
    --orange: #cf6e1c;
    --lemon: #d1a02d;
    --frankincense: #dba26c;
    --cedarwood: #9b5e50;
    --lavender: #3f2a7c;
  }
  * { box-sizing: border-box; margin: 0; padding: 0; }
  html, body { width: 1200px; height: 1180px; overflow: hidden; background: var(--page); }
  body { font-family: "Saira Condensed", "Arial Narrow", sans-serif; color: var(--ink); }

  .label-sheet {
    position: absolute; top: 92px; left: 40px; width: 1120px;
    display: flex; gap: 40px; align-items: flex-start;
  }
  .label-column { display: flex; flex-direction: column; gap: 24px; }

  /* 3in x 1in wrap label: 540 x 180 */
  .oil-label {
    position: relative; width: 540px; height: 180px;
    background: var(--label-white);
    border: 1px solid var(--label-edge);
    overflow: hidden;
  }
  .oil-band {
    position: absolute; left: 0; top: 108px; width: 472px; height: 72px;
    background: var(--tone);
  }

  /* left panel: warnings */
  .caution {
    position: absolute; top: 12px; left: 12px; width: 170px;
    font-size: 7.5px; line-height: 9.4px; color: var(--ink-soft);
  }
  .caution strong { font-weight: 700; color: var(--ink); }
  .ingredients {
    position: absolute; top: 120px; left: 12px; width: 170px;
    font-size: 8px; line-height: 10px; color: #ffffff;
  }
  .ingredients strong { font-weight: 600; }

  /* front panel */
  .front { position: absolute; top: 0; left: 190px; width: 282px; height: 180px; }
  .brand {
    position: absolute; top: 12px; left: 0; width: 100%;
    display: flex; flex-direction: column; align-items: center; gap: 5px;
  }
  .brand-mark { width: 18px; height: 18px; border: 1.5px solid var(--ink); border-radius: 4px; }
  .brand-name { font-size: 16px; font-weight: 400; letter-spacing: 5px; padding-left: 5px; line-height: 1; color: var(--ink); }

  .purity { position: absolute; top: 64px; left: 14px; }
  .purity-claim { font-size: 17px; font-weight: 500; line-height: 1; color: var(--tone); }
  .purity-badge {
    display: inline-block; margin-top: 3px; padding: 0 7px;
    font-size: 9px; font-weight: 600; line-height: 12px; color: #2f2a20;
    background: linear-gradient(90deg, var(--gold-dark), var(--gold), var(--gold-dark));
    border-radius: 6px;
  }
  .oil-name {
    position: absolute; top: 114px; left: 14px;
    font-size: 21px; font-weight: 600; line-height: 1.1; letter-spacing: 0.3px; color: #ffffff;
  }
  .oil-name.is-mid { font-size: 18px; top: 116px; }
  .oil-name.is-long { font-size: 14px; top: 119px; }
  .oil-volume {
    position: absolute; top: 160px; left: 14px;
    font-size: 7.5px; line-height: 1; color: rgba(255,255,255,0.92);
  }
  .botanical {
    position: absolute; top: 62px; right: 22px; width: 74px; height: 108px;
    border-radius: 8px;
    background: linear-gradient(180deg, color-mix(in srgb, var(--tone) 22%, transparent) 0%, color-mix(in srgb, #ffffff 35%, transparent) 100%);
  }

  /* barcode clearance: 3/8in */
  .barcode-zone {
    position: absolute; top: 0; right: 0; width: 68px; height: 100%;
    background: #ffffff; border-left: 1px solid var(--label-edge);
  }

  .rosemary { --tone: var(--rosemary); }
  .peppermint { --tone: var(--peppermint); }
  .eucalyptus { --tone: var(--eucalyptus); }
  .teatree { --tone: var(--teatree); }
  .orange { --tone: var(--orange); }
  .lemon { --tone: var(--lemon); }
  .frankincense { --tone: var(--frankincense); }
  .cedarwood { --tone: var(--cedarwood); }
  .lavender { --tone: var(--lavender); }
</style>
</head>
<body>
<main class="label-sheet">
  <div class="label-column">
    <article class="oil-label rosemary">
      <div class="oil-band"></div>
      <p class="caution"><strong>CAUTION: EYE AND SKIN IRRITANT.</strong> Avoid contact with eyes and skin. Wash hands after handling. If eye contact occurs, flush with water for 15 minutes. Not intended for topical or internal use. Contains Essential Oils. <strong>KEEP OUT OF REACH OF CHILDREN.</strong></p>
      <p class="ingredients"><strong>Ingredients:</strong> 100% pure essential oil, GC tested.</p>
      <div class="front">
        <div class="brand"><span class="brand-mark"></span><span class="brand-name">SOLVERA</span></div>
        <div class="purity"><p class="purity-claim">100% PURE</p><span class="purity-badge">ESSENTIAL OIL</span></div>
        <h2 class="oil-name">ROSEMARY</h2>
        <p class="oil-volume">0.33 fl oz (10 ml)</p>
        <div class="botanical" role="img" aria-label="Line drawing of a rosemary sprig"></div>
      </div>
      <div class="barcode-zone"></div>
    </article>
    <article class="oil-label peppermint">
      <div class="oil-band"></div>
      <p class="caution"><strong>CAUTION: EYE AND SKIN IRRITANT.</strong> Avoid contact with eyes and skin. Wash hands after handling. If eye contact occurs, flush with water for 15 minutes. Not intended for topical or internal use. Contains Essential Oils. <strong>KEEP OUT OF REACH OF CHILDREN.</strong></p>
      <p class="ingredients"><strong>Ingredients:</strong> 100% pure essential oil, GC tested.</p>
      <div class="front">
        <div class="brand"><span class="brand-mark"></span><span class="brand-name">SOLVERA</span></div>
        <div class="purity"><p class="purity-claim">100% PURE</p><span class="purity-badge">ESSENTIAL OIL</span></div>
        <h2 class="oil-name">PEPPERMINT</h2>
        <p class="oil-volume">0.33 fl oz (10 ml)</p>
        <div class="botanical" role="img" aria-label="Line drawing of peppermint leaves"></div>
      </div>
      <div class="barcode-zone"></div>
    </article>
    <article class="oil-label eucalyptus">
      <div class="oil-band"></div>
      <p class="caution"><strong>CAUTION: EYE AND SKIN IRRITANT.</strong> Avoid contact with eyes and skin. Wash hands after handling. If eye contact occurs, flush with water for 15 minutes. Not intended for topical or internal use. Contains Essential Oils. <strong>KEEP OUT OF REACH OF CHILDREN.</strong></p>
      <p class="ingredients"><strong>Ingredients:</strong> 100% pure essential oil, GC tested.</p>
      <div class="front">
        <div class="brand"><span class="brand-mark"></span><span class="brand-name">SOLVERA</span></div>
        <div class="purity"><p class="purity-claim">100% PURE</p><span class="purity-badge">ESSENTIAL OIL</span></div>
        <h2 class="oil-name is-mid">EUCALYPTUS</h2>
        <p class="oil-volume">0.33 fl oz (10 ml)</p>
        <div class="botanical" role="img" aria-label="Line drawing of a eucalyptus branch with buds"></div>
      </div>
      <div class="barcode-zone"></div>
    </article>
    <article class="oil-label teatree">
      <div class="oil-band"></div>
      <p class="caution"><strong>CAUTION: EYE AND SKIN IRRITANT.</strong> Avoid contact with eyes and skin. Wash hands after handling. If eye contact occurs, flush with water for 15 minutes. Not intended for topical or internal use. Contains Essential Oils. <strong>KEEP OUT OF REACH OF CHILDREN.</strong></p>
      <p class="ingredients"><strong>Ingredients:</strong> 100% pure essential oil, GC tested.</p>
      <div class="front">
        <div class="brand"><span class="brand-mark"></span><span class="brand-name">SOLVERA</span></div>
        <div class="purity"><p class="purity-claim">100% PURE</p><span class="purity-badge">ESSENTIAL OIL</span></div>
        <h2 class="oil-name">TEA TREE</h2>
        <p class="oil-volume">0.33 fl oz (10 ml)</p>
        <div class="botanical" role="img" aria-label="Line drawing of a tea tree sprig"></div>
      </div>
      <div class="barcode-zone"></div>
    </article>
    <article class="oil-label orange">
      <div class="oil-band"></div>
      <p class="caution"><strong>CAUTION: EYE AND SKIN IRRITANT.</strong> Avoid contact with eyes and skin. Wash hands after handling. If eye contact occurs, flush with water for 15 minutes. Not intended for topical or internal use. Contains Essential Oils. <strong>KEEP OUT OF REACH OF CHILDREN.</strong></p>
      <p class="ingredients"><strong>Ingredients:</strong> 100% pure essential oil, GC tested.</p>
      <div class="front">
        <div class="brand"><span class="brand-mark"></span><span class="brand-name">SOLVERA</span></div>
        <div class="purity"><p class="purity-claim">100% PURE</p><span class="purity-badge">ESSENTIAL OIL</span></div>
        <h2 class="oil-name">ORANGE</h2>
        <p class="oil-volume">0.33 fl oz (10 ml)</p>
        <div class="botanical" role="img" aria-label="Line drawing of a whole and halved orange"></div>
      </div>
      <div class="barcode-zone"></div>
    </article>
  </div>
  <div class="label-column">
    <article class="oil-label lemon">
      <div class="oil-band"></div>
      <p class="caution"><strong>CAUTION: EYE AND SKIN IRRITANT.</strong> Avoid contact with eyes and skin. Wash hands after handling. If eye contact occurs, flush with water for 15 minutes. Not intended for topical or internal use. Contains Essential Oils. <strong>KEEP OUT OF REACH OF CHILDREN.</strong></p>
      <p class="ingredients"><strong>Ingredients:</strong> 100% pure essential oil, GC tested.</p>
      <div class="front">
        <div class="brand"><span class="brand-mark"></span><span class="brand-name">SOLVERA</span></div>
        <div class="purity"><p class="purity-claim">100% PURE</p><span class="purity-badge">ESSENTIAL OIL</span></div>
        <h2 class="oil-name">LEMON</h2>
        <p class="oil-volume">0.33 fl oz (10 ml)</p>
        <div class="botanical" role="img" aria-label="Line drawing of a lemon and lemon slice"></div>
      </div>
      <div class="barcode-zone"></div>
    </article>
    <article class="oil-label frankincense">
      <div class="oil-band"></div>
      <p class="caution"><strong>CAUTION: EYE AND SKIN IRRITANT.</strong> Avoid contact with eyes and skin. Wash hands after handling. If eye contact occurs, flush with water for 15 minutes. Not intended for topical or internal use. Contains Essential Oils. <strong>KEEP OUT OF REACH OF CHILDREN.</strong></p>
      <p class="ingredients"><strong>Ingredients:</strong> 100% pure essential oil, GC tested.</p>
      <div class="front">
        <div class="brand"><span class="brand-mark"></span><span class="brand-name">SOLVERA</span></div>
        <div class="purity"><p class="purity-claim">100% PURE</p><span class="purity-badge">ESSENTIAL OIL</span></div>
        <h2 class="oil-name is-long">FRANKINCENSE</h2>
        <p class="oil-volume">0.33 fl oz (10 ml)</p>
        <div class="botanical" role="img" aria-label="Line drawing of a frankincense branch"></div>
      </div>
      <div class="barcode-zone"></div>
    </article>
    <article class="oil-label cedarwood">
      <div class="oil-band"></div>
      <p class="caution"><strong>CAUTION: EYE AND SKIN IRRITANT.</strong> Avoid contact with eyes and skin. Wash hands after handling. If eye contact occurs, flush with water for 15 minutes. Not intended for topical or internal use. Contains Essential Oils. <strong>KEEP OUT OF REACH OF CHILDREN.</strong></p>
      <p class="ingredients"><strong>Ingredients:</strong> 100% pure essential oil, GC tested.</p>
      <div class="front">
        <div class="brand"><span class="brand-mark"></span><span class="brand-name">SOLVERA</span></div>
        <div class="purity"><p class="purity-claim">100% PURE</p><span class="purity-badge">ESSENTIAL OIL</span></div>
        <h2 class="oil-name is-mid">CEDARWOOD</h2>
        <p class="oil-volume">0.33 fl oz (10 ml)</p>
        <div class="botanical" role="img" aria-label="Line drawing of cedar cones"></div>
      </div>
      <div class="barcode-zone"></div>
    </article>
    <article class="oil-label lavender">
      <div class="oil-band"></div>
      <p class="caution"><strong>CAUTION: EYE AND SKIN IRRITANT.</strong> Avoid contact with eyes and skin. Wash hands after handling. If eye contact occurs, flush with water for 15 minutes. Not intended for topical or internal use. Contains Essential Oils. <strong>KEEP OUT OF REACH OF CHILDREN.</strong></p>
      <p class="ingredients"><strong>Ingredients:</strong> 100% pure essential oil, GC tested.</p>
      <div class="front">
        <div class="brand"><span class="brand-mark"></span><span class="brand-name">SOLVERA</span></div>
        <div class="purity"><p class="purity-claim">100% PURE</p><span class="purity-badge">ESSENTIAL OIL</span></div>
        <h2 class="oil-name">LAVENDER</h2>
        <p class="oil-volume">0.33 fl oz (10 ml)</p>
        <div class="botanical" role="img" aria-label="Line drawing of lavender stems"></div>
      </div>
      <div class="barcode-zone"></div>
    </article>
  </div>
</main>
</body>
</html>
```